Verdanta Fund Partners business cards

Our company name is VERDANTA FUND PARTNERS. We need a business card for a start up company located in Medellin Colombia. The company will also be shortly expanding to USA. We are a Biotech company responsible for funding regenerative medicine projects with an emphasis on stem cell treatment and regeneration clinics. This will be a global company so the final design should communicate world wide financing for the new generation of regenerative medicine.

Industry/Entity Type

Business

```html
<!DOCTYPE html>
<html lang="en">
<head>
<meta charset="utf-8">
<title>Verdanta Fund Partners – Business Card</title>
<link rel="stylesheet" href="https://fonts.googleapis.com/css2?family=Jost:wght@400;500&display=swap">
<style>
  :root {
    --page-bg: #ebe7ee;
    --card-bg: #f7f7f7;
    --brand-purple: #6d1a7e;
    --edge-purple: #9a1fc0;
    --text-grey: #6b6b6b;
    --name-grey: #8a8a8a;
  }
  * { box-sizing: border-box; margin: 0; padding: 0; }
  html, body {
    width: 1200px;
    height: 1000px;
    overflow: hidden;
    background: var(--page-bg);
    font-family: "Jost", "Futura", sans-serif;
  }
  .canvas {
    position: relative;
    width: 1200px;
    height: 1000px;
  }
  .business-card {
    position: absolute;
    left: 150px;
    top: 243px;
    width: 900px;
    height: 514px;
    background: var(--card-bg);
    border-bottom: 4px solid var(--edge-purple);
    box-shadow: 0 18px 40px rgba(80, 30, 100, 0.22);
    overflow: hidden;
  }
  .card-curve {
    position: absolute;
    inset: 0;
    width: 100%;
    height: 100%;
  }
  .wordmark {
    position: absolute;
    left: 150px;
    top: 62px;
    display: flex;
    align-items: center;
    gap: 14px;
    color: var(--brand-purple);
    font-weight: 500;
    text-transform: uppercase;
    letter-spacing: 2px;
    line-height: 1.05;
  }
  .wordmark-dot {
    width: 22px;
    height: 22px;
    border-radius: 50%;
    background: var(--brand-purple);
  }
  .wordmark-name {
    font-size: 44px;
  }
  .wordmark-name span {
    display: block;
    font-size: 24px;
    letter-spacing: 5px;
  }
  .contact-list {
    position: absolute;
    left: 60px;
    top: 232px;
    list-style: none;
    color: var(--text-grey);
    font-size: 19px;
    line-height: 1.55;
    font-weight: 400;
  }
  .contact-list b {
    display: inline-block;
    width: 22px;
    font-weight: 400;
  }
  .person {
    position: absolute;
    right: 90px;
    top: 360px;
    text-align: left;
  }
  .person-name {
    color: var(--name-grey);
    font-size: 26px;
    font-weight: 400;
    letter-spacing: 0.5px;
  }
  .person-role {
    color: var(--brand-purple);
    font-size: 20px;
    font-weight: 400;
    margin-top: 2px;
  }
</style>
</head>
<body>
  <main class="canvas">
    <section class="business-card" aria-label="Verdanta Fund Partners business card">
      <svg class="card-curve" viewBox="0 0 900 514" aria-hidden="true">
        <path d="M 700 0 C 740 140, 600 210, 470 250 C 370 280, 340 360, 360 514"
              fill="none" stroke="var(--brand-purple)" stroke-width="4"/>
      </svg>

      <div class="wordmark">
        <div class="wordmark-dot"></div>
        <div class="wordmark-name">Verdanta<span>Fund Partners</span></div>
      </div>

      <ul class="contact-list">
        <li><b>m</b>+57 (0)4 321 5678</li>
        <li><b>t</b>+57 (0)4 321 5679</li>
        <li><b>e</b>sample.name@verdanta.co</li>
        <li><b>w</b>www.verdanta.co</li>
      </ul>

      <div class="person">
        <p class="person-name">Sample Name</p>
        <p class="person-role">CFO &amp; Founder</p>
      </div>
    </section>
  </main>
</body>
</html>
```